Design a New Business Card for Our Company

We are looking for fresh, unique, and a modern business card that reflects our roots as digital marketing agency focused on SEM.

Industry/Entity Type

Marketing

Contact Information for Business Card

looking for very unique out of the box designs. clean and modern that compliments our logo

Requirements
Must have
• colors should match our logo
• Front should have name, address, email, and phone/fax of the person, phone/fax are the same number
• back should have our url

```html
<!DOCTYPE html>
<html lang="en">
<head>
<meta charset="utf-8">
<title>Northlane Solutions – Business Card</title>
<link rel="stylesheet" href="https://fonts.googleapis.com/css2?family=Open+Sans:wght@400;700&display=swap">
<style>
  :root {
    --page-bg: #e4e4e4;
    --card-light: #f3f3f3;
    --brand-blue: #5b97d1;
    --brand-dark: #4a4a4a;
    --text-on-blue: #ffffff;
  }
  * { box-sizing: border-box; margin: 0; padding: 0; }
  html, body {
    width: 1200px;
    height: 900px;
    overflow: hidden;
    background: var(--page-bg);
    font-family: "Open Sans", sans-serif;
  }
  .business-card {
    position: absolute;
    left: 195px;
    top: 200px;
    width: 810px;
    height: 500px;
    display: flex;
    box-shadow: 0 10px 30px rgba(0,0,0,0.12);
  }
  .brand-side {
    width: 393px;
    background: var(--card-light);
    display: flex;
    align-items: center;
    justify-content: center;
    gap: 12px;
    padding-top: 40px;
  }
  .brand-mark {
    width: 26px;
    height: 26px;
    border-radius: 50%;
    background: var(--brand-blue);
    flex: none;
  }
  .brand-name {
    font-weight: 700;
    font-size: 34px;
    color: var(--brand-dark);
    letter-spacing: -0.5px;
  }
  .contact-side {
    flex: 1;
    background: var(--brand-blue);
    color: var(--text-on-blue);
    padding: 108px 40px 0 46px;
  }
  .person-name {
    font-weight: 700;
    font-size: 27px;
    line-height: 1.2;
  }
  .person-title {
    font-size: 22px;
    line-height: 1.3;
  }
  .address {
    margin-top: 22px;
    font-size: 21.5px;
    line-height: 1.38;
  }
  .contact-list {
    list-style: none;
    margin-top: 28px;
    font-size: 21px;
    line-height: 1.43;
  }
  .contact-list li {
    display: flex;
    align-items: center;
    gap: 12px;
  }
  .contact-list svg {
    width: 17px;
    height: 17px;
    fill: var(--text-on-blue);
    flex: none;
  }
</style>
</head>
<body>
  <div class="business-card">
    <div class="brand-side">
      <span class="brand-mark"></span>
      <span class="brand-name">Northlane Solutions</span>
    </div>
    <div class="contact-side">
      <p class="person-name">Daniel Carter</p>
      <p class="person-title">Managing Director</p>
      <p class="address">12345, Address Goes Here<br>Country Name, 123456.</p>
      <ul class="contact-list">
        <li>
          <svg viewBox="0 0 24 24" aria-hidden="true"><path d="M6.6 10.8c1.4 2.8 3.8 5.1 6.6 6.6l2.2-2.2c.3-.3.7-.4 1-.2 1.1.4 2.3.6 3.6.6.6 0 1 .4 1 1V20c0 .6-.4 1-1 1C10.6 21 3 13.4 3 4c0-.6.4-1 1-1h3.5c.6 0 1 .4 1 1 0 1.3.2 2.5.6 3.6.1.3 0 .7-.2 1L6.6 10.8z"/></svg>
          044-987 654 321
        </li>
        <li>
          <svg viewBox="0 0 24 24" aria-hidden="true"><path d="M7 2h8l3 3v5h1a2 2 0 0 1 2 2v8a2 2 0 0 1-2 2H5a2 2 0 0 1-2-2v-8a2 2 0 0 1 2-2h2V2zm2 2v6h7V6h-2V4H9zm-1 10v2h2v-2H8zm4 0v2h2v-2h-2zm4 0v2h2v-2h-2z"/></svg>
          044-987 654 321
        </li>
        <li>
          <svg viewBox="0 0 24 24" aria-hidden="true"><path d="M3 6h18v12H3V6zm2 2v.4l7 4.6 7-4.6V8H5z"/></svg>
          info@northlane.com
        </li>
        <li>
          <svg viewBox="0 0 24 24" aria-hidden="true"><path d="M12 2a10 10 0 1 0 0 20 10 10 0 0 0 0-20zm-1 17.9A8 8 0 0 1 4.2 10.8L9 15.6v1a2 2 0 0 0 2 2v1.3zm6.9-2.5A2 2 0 0 0 16 16h-1v-3a1 1 0 0 0-1-1H8v-2h2a1 1 0 0 0 1-1V7h2a2 2 0 0 0 2-2v-.4a8 8 0 0 1 2.9 12.8z"/></svg>
          www.northlane.com
        </li>
      </ul>
    </div>
  </div>
</body>
</html>
```